Institutional website for an IT Consulting company

Web design + HTML + CSS / Bootstrap + JS (interaction) integration in order to extend our existing website brightvale.coop.
Our website is currently aiming only for recruitment and not for customers, we want to provide a fluid transition between customer side website (this project) and recruitment website (existing site).

Ideally we would love the new design to be "inspired" by our actual graphic chart (Colors mainly). It should provide a great user experience and a landing page (or any mean) allowing the visitor to easily switch from the end customer front end (this project), the recruitment front end (existing front end https://www.brightvale.coop/) and the existing member front end (an other existing front end dedicated to members already existing).

In attachment you will find the expected site content mainly a one page with a first level of information and "link" to sub pages (a way to directly access this sub pages should also be provided).

The website should be accessible on mobile device and desktop.

The attachment is in french as it reflect the final site content, but if google translate isn't sufficient to have a general idea of the content, feel free to ask. We would love to have some visual representation for some categories.

Target Market(s)

fortune 500 companies

Industry/Entity Type

It Company

Coding

Coded - Design and coding required

Number of Pages Required

5+ page

Requirements
Must have
• This project must have an easy way to navigate between 3 sub sites, the customer one (the one designed here), the consultant / recruitment one (the existing one at brightvale.coop), the members one.

A one page experience at first leading to detail pages.

Custom made visuals to illustrate each categories.

Inspiration websites : pirog[.]fr ; tasklynn[.]com ; dorvelo[.] com ...

Be inspired by the existing color from our logo and existing website at brightvale[.]coop

```html
<!DOCTYPE html>
<html lang="en">
<head>
<meta charset="utf-8">
<title>Brightvale.coop</title>
<link href="https://fonts.googleapis.com/css2?family=Lato:wght@300;400;700;900&family=Montserrat:wght@400;500;600;700&display=swap" rel="stylesheet">
<style>
:root{
  --teal:#1aa3aa;
  --teal-dark:#13878d;
  --forest:#0c4a45;
  --forest-deep:#083d39;
  --ink:#222;
  --muted:#8a8a8a;
  --mist:#eef0f5;
  --paper:#f6f6f8;
  --white:#fff;
  --orange:#f07d2a;
  --navy:#1f5598;
  --green:#6d9e3a;
  --gold:#b59a2c;
}
*{box-sizing:border-box;margin:0;padding:0}
html,body{width:1200px;height:5190px;overflow:hidden}
body{font-family:'Lato',sans-serif;color:var(--ink);position:relative;background:var(--white)}
a{text-decoration:none;color:inherit}
.abs{position:absolute}
.btn{display:inline-flex;align-items:center;justify-content:center;font-family:'Montserrat',sans-serif;font-weight:600;font-size:13px;text-transform:uppercase;color:var(--white);height:42px;padding:0 24px}
.btn-dark{background:var(--forest)}
.btn-teal{background:var(--teal)}
.btn-line{border:2px solid var(--white);border-radius:4px}
.h2{font-family:'Montserrat',sans-serif;font-weight:600;font-size:32px;text-align:center;color:var(--ink)}
.h2 span{color:var(--teal)}
.logo{font-family:'Montserrat',sans-serif;font-weight:700;color:var(--forest);letter-spacing:1px}

/* hero */
.hero{left:0;top:0;width:1200px;height:600px;background:linear-gradient(110deg,#4a5560 0%,#8d99a3 45%,#c9d3da 80%,#e4ecf1 100%)}
.header{left:0;top:0;width:1200px;height:88px;background:rgba(255,255,255,.88)}
.header .logo{position:absolute;left:110px;top:18px;font-size:40px}
.header .logo small{display:block;font-size:15px;text-align:right;margin-top:-10px;color:var(--teal)}
.nav{position:absolute;right:110px;top:22px;display:flex;align-items:center;gap:54px;font-size:15px}
.nav a.active{color:var(--teal)}
.hero-title{left:110px;top:252px;width:500px;color:var(--white);font-size:25px;line-height:36px;font-weight:400}
.hero-btns{left:110px;top:384px;display:flex;gap:12px}
.dots{left:564px;top:552px;display:flex;gap:8px}
.dots i{width:10px;height:10px;border-radius:50%;background:rgba(255,255,255,.6)}
.dots i:first-child{background:var(--white)}

/* clients */
.clients{left:0;top:600px;width:1200px;height:145px;background:var(--mist)}
.client-row{position:absolute;left:150px;top:54px;width:900px;display:flex;justify-content:space-between;align-items:center;font-family:'Montserrat',sans-serif;font-weight:600;font-size:15px;color:#444}
.client-row span{display:flex;align-items:center;gap:8px}
.client-row b{width:22px;height:22px;border-radius:50%;background:#777;display:inline-block}

/* welcome */
.welcome{left:0;top:745px;width:1200px;height:470px}
.welcome-text{left:160px;top:82px;width:880px;text-align:center;color:var(--white)}
.welcome-text h2{font-family:'Montserrat',sans-serif;font-weight:600;font-size:36px;margin-bottom:22px}
.welcome-text p{font-size:14px;line-height:28px}
.welcome .btn{position:absolute;left:508px;top:286px;height:52px;width:184px}

/* i am */
.iam-photo{left:110px;top:1348px;width:588px;height:400px;background:linear-gradient(135deg,#2b2b2b,#6c5a46 55%,#bfb3a2)}
.iam-card{left:553px;top:1385px;width:537px;height:333px;background:var(--white);box-shadow:0 6px 24px rgba(0,0,0,.12);padding:24px 28px}
.iam-card h3{font-family:'Montserrat',sans-serif;font-weight:600;font-size:30px;margin-bottom:14px}
.iam-card h3 span{color:var(--teal)}
.iam-card p{font-size:13px;line-height:28px;color:var(--muted);margin-bottom:6px}
.iam-card .btns{display:flex;gap:12px;margin-top:14px}

/* join */
.join{left:110px;top:1862px;width:460px}
.join h3{font-family:'Montserrat',sans-serif;font-weight:600;font-size:30px;margin-bottom:26px}
.join h3 span{color:var(--teal)}
.join-item{margin-bottom:22px}
.join-item h4{font-size:16px;font-weight:400;margin-bottom:6px}
.join-item p{font-size:12px;line-height:28px;color:var(--muted);text-align:justify}
.join-item.active{border-left:2px solid var(--teal);margin-left:-8px;padding-left:6px}
.join-art{left:690px;top:1780px;width:510px;height:590px;background:linear-gradient(180deg,#d9ecf0 0%,#5fa8b3 50%,#1b4f63 100%)}

/* why */
.why{left:0;top:2420px;width:1200px;height:760px;background:var(--mist)}
.why .h2{position:absolute;top:116px;width:1200px}
.why-item{position:absolute;width:260px;text-align:center;font-size:12.5px;line-height:26px;color:#666}
.why-icon{width:112px;height:112px;border-radius:50%;margin:0 auto 22px;display:flex;align-items:center;justify-content:center}
.why-icon svg{width:52px;height:52px}
.ring{box-shadow:0 0 0 6px var(--mist),0 0 0 8px #bcc7cc}
.cta-band{left:0;top:3170px;width:1200px;height:150px}
.cta-band .btn{position:absolute;left:496px;top:58px;width:208px;height:52px}

/* testimonials */
.think .h2{position:absolute;top:3417px;left:0;width:1200px}
.quote{left:158px;top:3490px;width:884px;text-align:center;font-style:italic;font-size:15px;line-height:28px;color:#444}
.quote-by{left:0;top:3585px;width:1200px;text-align:center;font-size:18px;font-family:'Montserrat',sans-serif;font-weight:500}

/* insights */
.insights{left:0;top:3655px;width:1200px;height:590px;background:var(--paper)}
.insights .h2{position:absolute;top:118px;width:1200px}
.card{position:absolute;top:180px;width:315px}
.card .img{height:195px;position:relative}
.card .date{position:absolute;left:6px;top:0;width:34px;height:36px;background:var(--forest);color:var(--white);font-size:11px;font-weight:700;text-align:center;line-height:14px;padding-top:4px}
.card h4{font-family:'Montserrat',sans-serif;font-weight:500;font-size:19px;line-height:26px;margin:20px 0 16px}
.card .tag{font-size:13px;font-family:'Montserrat',sans-serif;margin-bottom:14px}
.card .more{font-size:14px;font-family:'Montserrat',sans-serif;font-weight:500;color:var(--teal);display:flex;align-items:center;gap:8px}

/* contact */
.contact .h2{position:absolute;top:4332px;left:0;width:1200px}
.contact-sub{left:340px;top:4385px;width:520px;text-align:center;font-family:'Montserrat',sans-serif;font-size:15px;line-height:28px;color:#444}
.map{left:110px;top:4460px;width:342px;height:262px;background:linear-gradient(135deg,#eceae4,#dfe6dd);box-shadow:0 2px 10px rgba(0,0,0,.15)}
.field{position:absolute;border:1px solid #ddd;background:var(--white);font-size:12px;color:#555;padding:14px 18px}
.send{left:585px;top:4692px;width:505px;height:44px;background:var(--teal);color:var(--white);font-family:'Montserrat',sans-serif;font-size:13px;font-weight:600;display:flex;align-items:center;justify-content:center}

/* footer */
.footer{left:0;top:4810px;width:1200px;height:315px;background:var(--forest)}
.footer .logo{position:absolute;left:110px;top:72px;width:270px;color:var(--white);font-size:36px}
.footer .logo small{display:block;font-size:16px;text-align:right;margin-top:-6px;padding-right:24px}
.footer-about{left:110px;top:150px;width:270px;font-size:12px;line-height:26px;color:var(--white)}
.fcol{position:absolute;top:78px;color:var(--white);font-size:12px}
.fcol h5{font-family:'Montserrat',sans-serif;font-size:15px;font-weight:500;margin-bottom:18px}
.fcol li{list-style:none;line-height:27px}
.fcol li i{display:inline-block;width:10px;height:10px;background:var(--white);margin-right:8px}
.news-input{width:206px;height:36px;background:var(--white);color:#888;font-size:11px;display:flex;align-items:center;justify-content:space-between;padding:0 10px;margin-top:16px}
.copy{left:0;top:5125px;width:1200px;height:65px;background:var(--forest-deep);color:var(--white);font-size:12px;text-align:center;line-height:65px}
</style>
</head>
<body>

<div class="abs hero" role="img" aria-label="Presenter in glasses beside a whiteboard in a bright office meeting room"></div>
<header class="abs header">
  <div class="logo">BRIGHTVALE<small>.COOP</small></div>
  <nav class="nav">
    <a class="active" href="#">Profile search</a>
    <a href="#">I am Brightvale</a>
    <a href="#">I want to join Brightvale</a>
    <a class="btn btn-teal" href="#">Contact us</a>
  </nav>
</header>
<h1 class="abs hero-title">BRIGHTVALE.COOP is a cooperative and participatory company specializing in digital services.</h1>
<div class="abs hero-btns"><a class="btn btn-dark" href="#">Contact us</a><a class="btn btn-teal" href="#">See the video</a></div>
<div class="abs dots"><i></i><i></i><i></i><i></i></div>

<section class="abs clients">
  <svg class="abs" style="left:108px;top:66px" width="16" height="28" viewBox="0 0 16 28"><path d="M14 2 2 14l12 12" fill="none" stroke="#666" stroke-width="2"/></svg>
  <div class="client-row">
    <span><b></b>Harlow Accountants</span>
    <span>Quenmark</span>
    <span><b style="border-radius:0"></b>Clients Logo</span>
    <span><b></b>Pivotline</span>
    <span><b></b>Nordwell Solutions</span>
  </div>
  <svg class="abs" style="left:1076px;top:66px" width="16" height="28" viewBox="0 0 16 28"><path d="M2 2l12 12L2 26" fill="none" stroke="#666" stroke-width="2"/></svg>
</section>

<section class="abs welcome">
  <svg class="abs" style="left:0;top:0" width="1200" height="470" viewBox="0 0 1200 470">
    <path d="M0 0H1200V420C1120 430 1080 430 1000 415 900 400 820 415 750 420 640 428 560 410 500 410 400 410 300 430 180 460 100 470 40 460 0 440Z" fill="var(--teal)"/>
    <path d="M0 440C40 460 100 470 180 460 300 430 400 410 500 410 560 410 640 428 750 420 820 415 900 400 1000 415 1080 430 1120 430 1200 420" fill="none" stroke="var(--teal)" stroke-width="3"/>
    <g fill="var(--white)" stroke="var(--teal)" stroke-width="3">
      <circle cx="178" cy="455" r="6"/><circle cx="340" cy="434" r="6"/><circle cx="502" cy="412" r="6"/><circle cx="638" cy="420" r="6"/><circle cx="778" cy="418" r="6"/><circle cx="900" cy="406" r="6"/><circle cx="1080" cy="430" r="6"/>
    </g>
  </svg>
  <div class="abs welcome-text">
    <h2>WELCOME TO BRIGHTVALE</h2>
    <p>Lorem ipsum dolor sit amet, consectetur adipiscing elit, sed do eiusmod tempor incididunt ut labore et dolore magna aliqua. Quis ipsum suspendisse ultrices gravida. Risus commodo viverra maecenas accumsan lacus vel facilisis. Lorem ipsum dolor sit amet, consectetur adipiscing elit, sed do eiusmod tempor incididunt ut labore et dolore magna aliqua. Quis ipsum suspendisse ultrices gravida. Risus commodo viverra maecenas accumsan lacus vel facilisis.</p>
  </div>
  <a class="btn btn-line" href="#">Get started &nbsp;➜</a>
</section>

<div class="abs iam-photo" role="img" aria-label="Team of developers working at laptops in a workshop"></div>
<div class="abs iam-card">
  <h3>I AM <span>BRIGHTVALE</span></h3>
  <p>Lorem ipsum dolor sit amet, consectetur adipiscing elit, sed do eid tempor incididunt ut labore et dolore magna aliqua.</p>
  <p>Lorem ipsum dolor sit amet, consectetur adipiscing elit, sed do eid tempor incididunt ut labore et dolore magna aliqua.</p>
  <p>Lorem ipsum dolor sit amet, consectetur adipiscing elit, sed do eid tempor incididunt ut labore et dolore magna aliqua.</p>
  <div class="btns"><a class="btn btn-dark" href="#">Learn more</a><a class="btn btn-teal" href="#">View jobs</a></div>
</div>

<div class="abs join-art" role="img" aria-label="Collage of professionals blended with a city skyline"></div>
<section class="abs join">
  <h3>I WANT TO <span>JOIN BRIGHTVALE</span></h3>
  <div class="join-item"><h4>Lorem ipsum dolor sit amet, consectetur adipiscing elit, ?</h4><p>Lorem ipsum dolor sit amet, consectetur adipiscing elit, sed do eiusmod tempor incididunt ut labore et dolore magna aliqua. Quis ipsum suspendisse ultrices gravida. Risus commodo viverra maecenas accumsan lacus vel facilisis.</p></div>
  <div class="join-item active"><h4>Lorem ipsum dolor sit amet, consectetur adipiscing elit, ?</h4><p>Lorem ipsum dolor sit amet, consectetur adipiscing elit, sed do eiusmod tempor incididunt ut labore et dolore magna aliqua. Quis ipsum suspendisse ultrices gravida. Risus commodo viverra</p></div>
  <div class="join-item"><h4>Lorem ipsum dolor sit amet, consectetur adipiscing elit, ?</h4><p>Lorem ipsum dolor sit amet, consectetur adipiscing elit, sed do eiusmod tempor incididunt ut labore et dolore magna aliqua. Quis ipsum suspendisse ultrices gravida. Risus commodo viverra maecenas accumsan lacus vel facilisis.</p></div>
</section>

<section class="abs why">
  <svg class="abs" style="left:0;top:-60px" width="1200" height="62" viewBox="0 0 1200 62"><path d="M0 62H1200V0Z" fill="var(--forest)"/></svg>
  <h2 class="h2">WHY <span>JOIN US?</span></h2>
  <div class="why-item" style="left:118px;top:185px"><div class="why-icon" style="background:var(--navy)"><svg viewBox="0 0 52 52" fill="none" stroke="#fff" stroke-width="2"><path d="M8 44h36M12 44V30M18 44V22M24 44V26M30 44V16M36 44V24M42 44V32"/></svg></div>For the equality of statutes and fairness in the valuation of work.</div>
  <div class="why-item" style="left:470px;top:185px"><div class="why-icon" style="background:var(--orange)"><svg viewBox="0 0 52 52" fill="none" stroke="#fff" stroke-width="2"><circle cx="26" cy="14" r="6"/><path d="M16 30c0-6 20-6 20 0M8 32h36v6H8zM14 38v8M38 38v8"/></svg></div>For the democratic mode of operation based on the principle of social and solidarity responsibility.</div>
  <div class="why-item" style="left:818px;top:185px"><div class="why-icon" style="background:var(--forest)"><svg viewBox="0 0 52 52" fill="none" stroke="#fff" stroke-width="2"><rect x="14" y="8" width="26" height="34"/><circle cx="18" cy="26" r="7"/><path d="M26 36h10M30 30h6M34 22v14"/></svg></div>For the cooperative legal framework that reconciles the advantages of employee status with the ambitions of entrepreneur status.</div>
  <div class="why-item" style="left:118px;top:460px"><div class="why-icon" style="background:var(--green)"><svg viewBox="0 0 52 52" fill="none" stroke="#fff" stroke-width="2"><rect x="10" y="10" width="32" height="32"/><path d="M18 34l16-16M28 18h6v6M24 34h-6v-6"/></svg></div>For the sharing of knowledge and mutual aid within a group of recognized experts in their field.</div>
  <div class="why-item" style="left:470px;top:460px"><div class="why-icon ring" style="background:var(--teal)"><svg viewBox="0 0 52 52" fill="none" stroke="#fff" stroke-width="2"><circle cx="26" cy="16" r="9"/><path d="M8 36h6l8 4h14l8-6M14 40v-8h10l6 4"/></svg></div>To contribute to the creation of a new model of entrepreneurship facing the model of traditional ESNs or IT services companies.</div>
  <div class="why-item" style="left:818px;top:460px"><div class="why-icon" style="background:var(--gold)"><svg viewBox="0 0 52 52" fill="none" stroke="#fff" stroke-width="2"><circle cx="22" cy="22" r="8"/><circle cx="34" cy="34" r="5"/><path d="M22 10v4M22 30v4M10 22h4M30 22h4"/></svg></div>To co-construct the digital world of tomorrow with a mode of shared governance.</div>
</section>

<section class="abs cta-band">
  <svg class="abs" style="left:0;top:0" width="1200" height="150" viewBox="0 0 1200 150"><path d="M0 0 1200 40V150H0Z" fill="var(--forest)"/></svg>
  <a class="btn btn-line" style="border-radius:0" href="#">Get started today</a>
</section>

<section class="think">
  <h2 class="h2">WHAT OUR <span>CLIENTS THINK</span></h2>
  <svg class="abs" style="left:92px;top:3516px" width="34" height="20" viewBox="0 0 34 20"><path d="M33 10H2M10 2 2 10l8 8" fill="none" stroke="#333" stroke-width="2"/></svg>
  <p class="abs quote">Lorem ipsum dolor sit amet, consectetur adipiscing elit, sed do eiusmod tempor incididunt ut labore et dolore magna aliqua. Quis ipsum suspendisse ultrices gravida. Risus commodo viverra maecenas accumsan lacus vel facilisis. Lorem ipsum dolor sit amet, consectetur adipiscing elit, sed do eiusmod tempor incididunt ut labore et dolore magna aliqua.</p>
  <svg class="abs" style="left:1066px;top:3516px" width="34" height="20" viewBox="0 0 34 20"><path d="M1 10h31M24 2l8 8-8 8" fill="none" stroke="#333" stroke-width="2"/></svg>
  <p class="abs quote-by">Chief Growth Officer</p>
</section>

<section class="abs insights">
  <h2 class="h2">OUR LATEST <span>INSIGHTS</span></h2>
  <article class="card" style="left:110px"><div class="img" role="img" aria-label="Hands on a laptop keyboard in a meeting" style="background:linear-gradient(135deg,#3a3a3a,#8a6a50)"><div class="date">Jan<br>10</div></div><h4>The standard Lorem Ipsum passage</h4><p class="tag">DATA ANALYTICSLOGISTICS</p><a class="more" href="#">LEARN MORE ➜</a></article>
  <article class="card" style="left:442px"><div class="img" role="img" aria-label="Skyscrapers seen from below against a blue sky" style="background:linear-gradient(180deg,#9fc3df,#2c4a66)"><div class="date">Jan<br>10</div></div><h4>The standard Lorem Ipsum passage</h4><p class="tag">DATA ANALYTICSLOGISTICS</p><a class="more" href="#">LEARN MORE ➜</a></article>
  <article class="card" style="left:774px"><div class="img" role="img" aria-label="Young team gathered around a laptop" style="background:linear-gradient(135deg,#e6e2dc,#6b5e55)"><div class="date">Jan<br>10</div></div><h4>The standard Lorem Ipsum passage</h4><p class="tag">DATA ANALYTICSLOGISTICS</p><a class="more" href="#">LEARN MORE ➜</a></article>
</section>

<section class="contact">
  <h2 class="h2">READY TO START <span>THE CONVERSATION?</span></h2>
  <p class="abs contact-sub">We would love to hear from you, please fill in the form below and a member of our team will contact you.</p>
  <div class="abs map" role="img" aria-label="Street map showing the office location"></div>
  <div class="field" style="left:585px;top:4468px;width:252px;height:48px">Name*</div>
  <div class="field" style="left:845px;top:4468px;width:245px;height:48px">Email*</div>
  <div class="field" style="left:585px;top:4525px;width:505px;height:48px">Subject</div>
  <div class="field" style="left:585px;top:4582px;width:505px;height:100px">Message*</div>
  <a class="abs send" href="#">SEND MESSAGE</a>
</section>

<footer class="abs footer">
  <div class="logo">BRIGHTVALE<small>.COOP</small></div>
  <p class="abs footer-about">Lorem ipsum dolor sit amet, cotur adipiscing elit, sed do eiusmod tempor incidnt ut labore et dolore magna aliqua. Quis ium suspendisse ultrices gravida. Risus commodo</p>
  <div class="fcol" style="left:438px"><h5>Company</h5><ul><li>Home</li><li>About</li><li>Our Solution</li><li>Our Work</li><li>Insights</li><li>Careers</li></ul></div>
  <div class="fcol" style="left:570px"><h5>Help</h5><ul><li>Contact Us</li><li>FAQ</li><li>Privacy Policy</li><li>Feedback</li><li>Sitemap</li></ul></div>
  <div class="fcol" style="left:710px;width:210px"><h5>Signup for our Newsletter</h5><p style="line-height:22px">Lorem ipsumconsect elit, sed do eiusmod tempor</p><div class="news-input">Enter you email<svg width="16" height="14" viewBox="0 0 16 14"><path d="M1 7 15 1 11 13 8 8Z" fill="var(--teal)"/></svg></div></div>
  <div class="fcol" style="left:972px"><h5>Connect with us</h5><ul><li><i></i>Friendwall</li><li><i></i>Chirper</li><li><i></i>Snapgrid</li><li><i></i>Workmesh</li></ul></div>
</footer>
<div class="abs copy">Copyright © 2020 BRIGHTVALE All Rights Reserved.</div>

</body>
</html>
```